Striking new Advert required for Commercial Real Estate Agency

We need a a NEW newspaper advertisement for the marketing of a large commercial property (a Backpackers lodge)

Dimensions are to be width of 101mm and height of 100mm (10cms)

Our key design statement for this advert is clean, modern and minimalist design, with accents of 'HOT PINK' colour to remove it from looking too boring, perhaps in the area of the contact icons. The heirachy of the advert is outlined in the attached ADVERTISEMENT TEXT FILE.

Our company name is THE HARBOURLINE COLLECTIVE, and we want our brand to appear professional yet classy in it's design style (sort of like an advertising or design agency)

We have two logo options below, one more square in its layout (which we prefer) and the other more rectangular, which may be better suited for the layout. We are not adverse to the logo being reversed (white text on black), along with other key element areas such as the main advert heading and the "FOR SALE" part, and think this would be a good option.
There are two photos attached to be included in the advert.

We have attached an example of an old advert that we did, which we DID NOT LIKE, and which was for a smaller width than the one we need (it is only 65% of the width of this one). WE have also atached a file showing layout of some of our competitors adverts, which we dont think are too good either.

We are really open for ideas, but have time pressures, so please come back with any questions as soon as you can, if needed.

Thank you
Updates

Thank you for the great and diverse designs. There are a few standout options, but one style that we prefer most.

Target Market(s)

We are wanting this newspaper advertisement to attract interest from real estat e developers, investors and motel/lodge owners, along with other high nett worth individuals

Industry/Entity Type

Real Estate

Font styles to use
Serif
Sans Serif

Colors
1b1b1b
a54499
474747
fbfbfb

Requirements
Must have
• Clean modern look, predominantly monochromatic or black and white, with the hot pink accent somewhere, as mentioned above.
• All the contents of the TEXT provided, perhaps with additional space to add a little more if needed, Please advise if you think we dont have enough space for all of the TEXT
Should not have
• Script like fonts
• Cartoonish characters
• a 'cheap' look

```html
<!DOCTYPE html>
<html lang="en">
<head>
<meta charset="utf-8">
<title>For Sale – Mount Victoria Land Grab</title>
<link href="https://fonts.googleapis.com/css2?family=Montserrat:wght@400;500;800&family=Source+Sans+3:wght@400;600;700&display=swap" rel="stylesheet">
<style>
  :root{
    --ink:#1b1b1b;
    --pink:#a54499;
    --band:#474747;
    --paper:#fbfbfb;
    --body:#2c2c2c;
    --page:#e4e4e4;
  }
  *{box-sizing:border-box;margin:0;padding:0}
  html,body{width:1200px;height:903px;overflow:hidden;background:var(--page)}
  .advert{
    position:absolute;left:160px;top:16px;width:880px;height:870px;
    background:#fff;display:flex;flex-direction:column;
    font-family:"Source Sans 3",sans-serif;color:var(--body);
    box-shadow:0 2px 10px rgba(0,0,0,.15);
  }
  .masthead{height:96px;display:flex;justify-content:space-between;align-items:flex-end;padding:0 43px 12px 41px}
  .masthead h1{font-family:"Montserrat",sans-serif;font-weight:800;font-size:68px;line-height:1;color:var(--ink);letter-spacing:1px;margin-bottom:6px}
  .masthead .tagline{font-size:26px;color:var(--ink);font-weight:400;margin-bottom:2px}
  .hero{height:251px;background:linear-gradient(180deg,#b7c6cf 0%,#9aa7a6 28%,#8a9178 55%,#6f7d55 80%,#55673c 100%)}
  .address-band{height:63px;background:var(--band);color:var(--paper);display:flex;align-items:center;justify-content:center;font-family:"Montserrat",sans-serif;font-weight:400;font-size:27px;letter-spacing:.5px}
  .details{flex:1;padding:6px 46px 0 41px}
  .intro{font-size:22px;line-height:29px;margin-bottom:4px}
  .lead{color:var(--pink);font-weight:700;font-size:22px;line-height:29px;margin-bottom:6px}
  .features{list-style:none}
  .features li{position:relative;padding-left:35px;font-size:22px;line-height:29px;margin-bottom:8px;text-align:justify}
  .features li::before{content:"";position:absolute;left:8px;top:12px;width:8px;height:8px;border-radius:50%;background:var(--pink)}
  .features sup{font-size:12px;line-height:0}
  .tender{text-align:center;color:var(--pink);font-weight:700;font-size:22px;margin-top:12px}
  .contact-bar{height:122px;background:var(--ink);color:var(--paper);display:flex;align-items:center;padding:0 41px}
  .agent{width:216px}
  .agent .name{font-size:24px;font-weight:600;margin-bottom:6px}
  .line{display:flex;align-items:center;gap:12px;font-size:22px;line-height:31px}
  .line svg{width:16px;height:16px;flex:none}
  .channels{width:395px;padding-top:22px}
  .brand{display:flex;align-items:center;gap:12px;margin-left:auto}
  .brand .mark{width:58px;height:58px;border:3px solid var(--paper)}
  .brand .wordmark{font-family:"Montserrat",sans-serif;font-weight:500;font-size:17px;line-height:20px;letter-spacing:1px;color:var(--paper)}
</style>
</head>
<body>
<main class="advert">
  <header class="masthead">
    <h1>FOR SALE</h1>
    <p class="tagline">Mount Victoria Land Grab</p>
  </header>
  <div class="hero" role="img" aria-label="Aerial photograph of the lodge and surrounding hillside suburb with rooftops and trees"></div>
  <div class="address-band">Marella’s Lodge, 48 Kelburn Terrace, Mount Victoria</div>
  <section class="details">
    <p class="intro">This Old Beauty has served many, and is now ripe for development.</p>
    <p class="lead">One of Mt Vic’s largest land areas, now offered with vacant possession, with key details being:</p>
    <ul class="features">
      <li>Large Land area of 2076m<sup>2</sup> with elevated sunny position and great outlook + access from Halden Street</li>
      <li>Existing Backpackers Lodge of 970m<sup>2</sup> providing multiple rooms with amenity areas</li>
      <li>Four adjacent sites also available, taking total land area to 4452m<sup>2</sup>, an unprecedented Land Offering in this popular cuity fringe location</li>
    </ul>
    <p class="tender">Now Selling by Closed Tender</p>
  </section>
  <footer class="contact-bar">
    <div class="agent">
      <p class="name">Miles Ardern</p>
      <p class="line"><svg viewBox="0 0 16 16"><path d="M4 1.5l2.5 3-1.5 1.8c.8 1.8 2.2 3.2 4 4l1.8-1.5 3 2.5-1.5 2.5C7 13.5 2.5 9 1.5 3z" fill="none" stroke="var(--pink)" stroke-width="1.4"/></svg>(04) 555 0182</p>
      <p class="line"><svg viewBox="0 0 16 16"><rect x="4" y="1" width="8" height="14" rx="1.5" fill="none" stroke="var(--pink)" stroke-width="1.4"/><rect x="7" y="12" width="2" height="1" fill="var(--pink)"/></svg>(021) 555 247</p>
    </div>
    <div class="channels">
      <p class="line"><svg viewBox="0 0 16 16"><rect x="2" y="4" width="12" height="8" fill="var(--pink)"/><path d="M2 4l6 5 6-5" fill="none" stroke="var(--ink)" stroke-width="1"/></svg>miles@harbourline.co.nz</p>
      <p class="line"><svg viewBox="0 0 16 16"><g fill="none" stroke="var(--pink)" stroke-width="1.2"><circle cx="8" cy="8" r="6"/><ellipse cx="8" cy="8" rx="2.5" ry="6"/><path d="M2 8h12M3 5h10M3 11h10"/></g></svg>www.harbourline.co.nz</p>
    </div>
    <div class="brand">
      <span class="mark"></span>
      <span class="wordmark">THE<br>HARBOURLINE<br>COLLECTIVE</span>
    </div>
  </footer>
</main>
</body>
</html>
```